Stationary design for new digital markerting company

I need a stationary design for a new digital marketing company called Mossy Lantern.
We work with businesses to help them create and increase their online presence in order to increase awareness of their brand.
The design must keep with the colour schemes of our logo.
I would like a design that stands out but isn't over the top while also being professional and sophisticated.

Target Market(s)

other businesses

Industry/Entity Type

Business Consultant

Font styles to use
Sans Serif

Colors
abd036
ffffff
a54499

Requirements
Must have
• logo, plus the same colour scheme

```html
<!DOCTYPE html>
<html lang="en">
<head>
<meta charset="utf-8">
<title>Mossy Lantern — Business Cards</title>
<link rel="stylesheet" href="https://fonts.googleapis.com/css2?family=Montserrat:wght@400;700&display=swap">
<style>
  :root {
    --purple: #a54499;
    --purple-deep: #a01f86;
    --green: #abd036;
    --green-deep: #7dba1e;
    --white: #ffffff;
    --paper: #eef0f3;
    --backdrop: #e5e4e9;
    --ink: #2a2a2a;
    --ink-soft: #3c3c3c;
  }
  * { box-sizing: border-box; margin: 0; padding: 0; }
  html, body {
    width: 1200px; height: 934px; overflow: hidden;
    background: var(--backdrop);
    font-family: "Montserrat", sans-serif;
  }
  .sheet {
    position: relative; width: 1200px; height: 934px;
    display: flex; flex-direction: column; align-items: center; justify-content: center; gap: 44px;
  }
  .card {
    position: relative; width: 700px; height: 400px; overflow: hidden;
    box-shadow: 0 10px 28px rgba(60, 40, 70, 0.18);
  }
  .card-art { position: absolute; inset: 0; width: 100%; height: 100%; }

  /* Back of card */
  .card--back { background: var(--purple-deep); }
  .back-brand {
    position: absolute; left: 0; right: 0; top: 118px;
    display: flex; flex-direction: column; align-items: center; gap: 22px;
  }
  .brand-dot { width: 92px; height: 92px; border-radius: 50%; background: var(--green-deep); }
  .brand-name {
    font-weight: 700; font-size: 40px; line-height: 48px; letter-spacing: 2px; text-transform: uppercase;
    color: var(--white);
  }

  /* Front of card */
  .card--front { background: var(--paper); }
  .front-brand {
    position: absolute; right: 46px; top: 62px;
    display: flex; flex-direction: column; align-items: center; gap: 16px;
  }
  .front-brand .brand-dot { width: 96px; height: 96px; box-shadow: 0 0 0 12px var(--paper); }
  .front-brand .brand-name { color: var(--purple-deep); font-size: 36px; line-height: 44px; }

  .contact { position: absolute; left: 54px; top: 176px; color: var(--ink); }
  .contact-name { font-weight: 700; font-size: 21px; line-height: 26px; letter-spacing: 0.5px; text-transform: uppercase; }
  .contact-role { font-size: 16px; line-height: 20px; color: var(--ink-soft); }
  .contact-lines { list-style: none; margin-top: 18px; }
  .contact-lines li {
    display: flex; align-items: center; gap: 12px;
    font-size: 15px; line-height: 22px; color: var(--ink-soft);
  }
  .icon { width: 18px; height: 18px; flex: none; }
  .contact-address { margin-top: 12px; font-size: 15px; line-height: 20px; color: var(--ink-soft); font-style: normal; }
</style>
</head>
<body>
<main class="sheet">

  <section class="card card--back" aria-label="Business card back">
    <svg class="card-art" viewBox="0 0 700 400" aria-hidden="true">
      <circle cx="330" cy="190" r="190" fill="#ffffff" fill-opacity="0.07"/>
    </svg>
    <div class="back-brand">
      <span class="brand-dot"></span>
      <span class="brand-name">Mossy Lantern</span>
    </div>
  </section>

  <section class="card card--front" aria-label="Business card front">
    <svg class="card-art" viewBox="0 0 700 400" preserveAspectRatio="none" aria-hidden="true">
      <path d="M0 0 H700 V40 Q360 70 0 150 Z" fill="#a01f86"/>
      <path d="M0 150 Q360 70 700 40 V50 Q360 82 0 166 Z" fill="#7dba1e"/>
      <path d="M0 388 Q380 378 700 262 V270 Q380 386 0 394 Z" fill="#7dba1e"/>
      <path d="M0 400 V394 Q380 386 700 270 V400 Z" fill="#a01f86"/>
    </svg>

    <div class="front-brand">
      <span class="brand-dot"></span>
      <span class="brand-name">Mossy Lantern</span>
    </div>

    <div class="contact">
      <h1 class="contact-name">Dana Whitfield</h1>
      <p class="contact-role">Managing Director</p>
      <ul class="contact-lines">
        <li>
          <svg class="icon" viewBox="0 0 18 18" aria-hidden="true">
            <rect width="18" height="18" rx="3" fill="#7dba1e"/>
            <path d="M5 4 L7.5 4 L8.3 6.8 L7 7.8 Q8.2 10.2 10.3 11.2 L11.3 10 L14 10.8 L14 13.2 Q8.5 14 4.8 8.8 Q4 6.5 5 4 Z" fill="#fff"/>
          </svg>
          1300 555 018
        </li>
        <li>
          <svg class="icon" viewBox="0 0 18 18" aria-hidden="true">
            <rect width="18" height="18" rx="3" fill="#7dba1e"/>
            <rect x="3.5" y="5" width="11" height="8" fill="#fff"/>
            <path d="M3.5 5 L9 9.5 L14.5 5" fill="none" stroke="#7dba1e" stroke-width="1.2"/>
          </svg>
          info@mossylantern.com
        </li>
        <li>
          <svg class="icon" viewBox="0 0 18 18" aria-hidden="true">
            <rect width="18" height="18" rx="3" fill="#7dba1e"/>
            <circle cx="9" cy="9" r="5" fill="none" stroke="#fff" stroke-width="1.3"/>
            <path d="M4 9 H14 M9 4 Q6 9 9 14 M9 4 Q12 9 9 14" fill="none" stroke="#fff" stroke-width="1.1"/>
          </svg>
          www.mossylantern.com
        </li>
      </ul>
      <address class="contact-address">Level 12, Harbour House<br>18 Quay Lane, Sydney</address>
    </div>
  </section>

</main>
</body>
</html>
```